Business Card design project for new family-run construction business

We need a logo and business card designed for a new construction company. We want to convey a professional, but approachable image. We hope to be servicing small residential clients as well as large commercial contracts as well.
Our business will employ a single "Hydro excavator" truck, which can be used for multiple purposes: vacuuming up dirt or water, digging holes, clearing sewer blockages and so on.
We are open to different colour schemes, however blue and white, or yellow/green would be good combinations. We are open to multiple colours (2-4), so long as they are complimentary.

EDIT: Let's not put much emphasis on the octopus... unless it's very clear that the arms are actual vacuum hoses, it won't make sense. An octopus on it's own has little to do with our business.

Please also do not use actual photos of hydro-vac trucks. This is not the aesthetic we are going for.

**The logo should instead be: A stylized outline of a hydrovac truck (a line drawing or digital version of a line-drawing). See the two examples in the attached images of hydrovac trucks. I've also included a very crude pen outline as a reference. Please use your artistic discretion and talent (as I clearly have none) to make something that looks much nicer. Thanks for your efforts!**

The front of the card should have the following elements:
Logo
Name: R & T Hydro Excavation and Flushign
Two phone numbers: Direct and Office
Email address
Website
It should also have the name of the employee and their job title
At the bottom of the card it should say (in a noticeable way): "24/7 Emergency Calls Welcome"

The back of the card should have the following elements:
"20 Years Experience"
"A Canadian Family Run Business"
A small maple-leaf logo that is in a similar style to the rest of the card/logos in the bottom right corner of the back of the card. (see attached)

**We have just added a number of business card designs that really appeal to us to offer inspiration.**

Reason: We have not received designs that hit the mark of what we are looking for. Feedback has been posted, so we would like to provide the designers more time.

Target Market(s)

Commercial and residential customers. As big as large malls and office buildings, as small single-family home owners

Industry/Entity Type

Construction Company

Contact Information for Business Card

We have just added a number of business card designs that really appeal to us to offer inspiration.

Logo
Email address
Website

"20 Years Experience"

Logo Text

R & T Hydro Excavation and Flushing

Font styles to use
Serif
Sans Serif
Other font styles liked:
• Helvetica, Futura, Impact, bold strong, modern fonts that convey a sense of design and style

Colors
0592cd
ec1f27
9bcb3c

Requirements
Must have
• The front of the card should have the following elements:
• Logo
• Name: R & T Hydro Excavation and Flushign
• Two phone numbers: Direct and Office
• Email address
• Website
• It should also have the name of the employee and their job title
• At the bottom of the card it should say (in a noticeable way): "24/7 Emergency Calls Welcome"
• The back of the card should have the following elements:
• "20 Years Experience"
• "A Canadian Family Run Business"
• A small maple-leaf logo that is in a similar style to the rest of the card/logos in the bottom right corner of the back of the card. (see attached)
Nice to have
• The card does not have to be a perfect rectangle. We are open to rounded corners or cut out elements.
• Also embossing, engraving, adding highlighted/glossy layers (spot glass?), or any other effect that will give the card a unique look/feel is more than welcome.
• We would love to have a card that stands out from others and is compelling to look at it, so we are happy to incorporate any sort of modern printing technology to bring out the design.
• Please feel encouraged to be creative and design something unique, especially for this industry.
• Our dream would be if a Scandinavian architect were to go into the construction business and design this business card ;)
Should not have
• Photographs

```html
<!DOCTYPE html>
<html lang="en">
<head>
<meta charset="utf-8">
<title>R &amp; T Hydro Excavation and Flushing – Business Card</title>
<link rel="stylesheet" href="https://fonts.googleapis.com/css2?family=Arimo:wght@400;700&family=Tinos:wght@400&display=swap">
<style>
  :root {
    --backdrop: #4d4d4f;
    --card: #151516;
    --blue: #1e9ad6;
    --white: #f4f4f4;
    --band-grey: #5c5c5e;
  }
  * { box-sizing: border-box; margin: 0; padding: 0; }
  html, body { width: 801px; height: 1200px; overflow: hidden; }
  body {
    background: var(--backdrop);
    font-family: "Arimo", Arial, sans-serif;
    color: var(--white);
    position: relative;
  }
  .card {
    position: absolute;
    left: 50px;
    width: 701px;
    height: 400px;
    background: var(--card);
    overflow: hidden;
  }
  .card--back { top: 110px; }
  .card--front { top: 680px; }

  .brand {
    position: absolute;
    display: flex;
    align-items: center;
    gap: 12px;
    font-weight: 400;
    color: var(--white);
    white-space: nowrap;
  }
  .brand__mark { width: 20px; height: 20px; background: var(--blue); flex: none; }
  .card--back .brand { left: 50%; top: 120px; transform: translateX(-50%); font-size: 28px; }
  .card--front .brand { left: 36px; top: 58px; font-size: 26px; }

  .tagline {
    position: absolute;
    left: 0; right: 0; top: 222px;
    text-align: center;
    color: var(--blue);
    font-size: 26px;
    line-height: 36px;
  }

  .person { position: absolute; left: 36px; top: 138px; }
  .person__name { color: var(--blue); font-size: 19px; text-transform: uppercase; }
  .person__title { font-size: 15px; margin-top: 2px; }
  .rule {
    position: absolute; left: 36px; top: 188px;
    width: 620px; height: 2px; background: var(--blue);
  }

  .contacts { position: absolute; left: 36px; top: 208px; list-style: none; }
  .contacts li {
    display: flex; align-items: center; gap: 10px;
    font-size: 19px; line-height: 27px;
  }
  .contacts svg { width: 13px; height: 13px; fill: var(--blue); flex: none; }

  .address {
    position: absolute; right: 40px; top: 262px;
    font-size: 18px; line-height: 23px; text-align: left;
  }
  .emergency { position: absolute; left: 300px; top: 318px; display: flex; align-items: baseline; gap: 16px; }
  .emergency__hours { color: var(--blue); font-size: 36px; font-weight: 700; }
  .emergency__note { font-family: "Tinos", "Times New Roman", serif; font-size: 19px; letter-spacing: 1px; }

  .band { position: absolute; bottom: 0; height: 24px; }
  .band--blue { left: 0; width: 290px; background: var(--blue); }
  .band--grey { left: 290px; right: 0; background: var(--band-grey); }
</style>
</head>
<body>

  <section class="card card--back" aria-label="Card back">
    <div class="brand"><span class="brand__mark"></span>R &amp; T Hydro Excavation and Flushing</div>
    <p class="tagline">20 Years Experience<br>A Canadian Family Run Business</p>
  </section>

  <section class="card card--front" aria-label="Card front">
    <div class="brand"><span class="brand__mark"></span>R &amp; T Hydro Excavation and Flushing</div>

    <div class="person">
      <p class="person__name">Employee Name</p>
      <p class="person__title">Title</p>
    </div>
    <div class="rule"></div>

    <ul class="contacts">
      <li><svg viewBox="0 0 12 12"><rect x="3" y="0" width="6" height="12" rx="1"/></svg>800.555.0142</li>
      <li><svg viewBox="0 0 12 12"><path d="M2 0h3l1 3-2 1.5a7 7 0 0 0 3.5 3.5L9 6l3 1v3a2 2 0 0 1-2 2A10 10 0 0 1 0 2a2 2 0 0 1 2-2z"/></svg>800.555.0187</li>
      <li><svg viewBox="0 0 12 12"><path d="M0 2h12v1L6 7 0 3zM0 4.5l6 4 6-4V10H0z"/></svg>info@rthydro.ca</li>
      <li><svg viewBox="0 0 12 12"><circle cx="6" cy="6" r="5.5" fill="none" stroke="#1e9ad6" stroke-width="1"/><path d="M0.5 6h11M6 0.5v11" stroke="#1e9ad6" stroke-width="1"/></svg>www.rthydro.ca</li>
    </ul>

    <p class="address">48th Street SW Suite 210,<br>Ottawa ON K2P 1L4</p>

    <div class="emergency">
      <span class="emergency__hours">24/7</span>
      <span class="emergency__note">Emergency Calls Welcome</span>
    </div>

    <div class="band band--blue"></div>
    <div class="band band--grey"></div>
  </section>

</body>
</html>
```